Business Card for my New Brokerage

Looking to get a business card design for my new Real Estate Brokerage.
I want it with Picture, Phone Number, Email, Website, Office Address
Name and Designation. Please add logo too.

Target Market(s)

Real Estate Investors or Home Buyers

Industry/Entity Type

Real Estate

Contact Information for Business Card

Name, Email, Phone Number, website, email, office address

Colors
EB3D1F
EC4F4E
F09395
F8D3D4
FCEDEE

Requirements
Must have
• Minimalistic, Clean, Modern, Photo
Nice to have
• White and Red Colors

```html
<!DOCTYPE html>
<html lang="en">
<head>
<meta charset="utf-8">
<title>Ember Realty Inc – Business Card</title>
<link rel="stylesheet" href="https://fonts.googleapis.com/css2?family=Roboto:wght@400;500;700&display=swap">
<style>
  :root {
    --brand-red: #e53a44;
    --brand-red-deep: #d81e2a;
    --brand-red-light: #ec4f4e;
    --ink: #555457;
    --rule: #8a8a8a;
    --paper: #fbfbfb;
    --on-red: #f4f4f4;
    --backdrop: #2a2a2c;
  }
  * { box-sizing: border-box; margin: 0; padding: 0; }
  html, body {
    width: 1200px; height: 900px; overflow: hidden;
    background: var(--backdrop);
    font-family: "Roboto", Arial, sans-serif;
  }
  .stage {
    width: 1200px; height: 900px;
    display: flex; flex-direction: column; align-items: center; justify-content: center;
    gap: 40px;
  }
  .card {
    position: relative;
    width: 665px; height: 380px;
    border-radius: 4px;
    overflow: hidden;
    box-shadow: 0 12px 30px rgba(0,0,0,.45);
  }

  /* Front */
  .card-front { background: var(--paper); }
  .holder { position: absolute; left: 44px; top: 62px; }
  .holder-name {
    color: var(--brand-red); font-weight: 700; font-size: 22px; letter-spacing: .5px;
    text-transform: uppercase;
  }
  .holder-title { color: var(--ink); font-weight: 500; font-size: 18px; margin-top: 2px; }
  .contact-list { list-style: none; margin-top: 14px; }
  .contact-item {
    display: flex; align-items: center; gap: 10px;
    color: var(--ink); font-size: 17px; line-height: 28px;
  }
  .contact-icon { width: 16px; height: 16px; flex: none; }

  .company-name {
    position: absolute; right: 48px; top: 150px;
    display: flex; align-items: center; gap: 10px;
    font-weight: 700; font-size: 34px; line-height: 1;
    color: var(--brand-red); white-space: nowrap;
  }
  .company-mark { width: 12px; height: 12px; border-radius: 50%; background: var(--brand-red); flex: none; }

  .divider {
    position: absolute; left: 330px; right: 48px; top: 240px;
    height: 1px; background: var(--rule);
  }
  .office-address {
    position: absolute; right: 48px; top: 256px;
    text-align: right; font-style: normal;
    color: var(--ink); font-size: 17px; line-height: 26px;
  }

  /* Back */
  .card-back {
    background: radial-gradient(ellipse at 40% 30%, var(--brand-red-light) 0%, var(--brand-red-deep) 75%);
    display: flex; align-items: center; justify-content: center;
  }
  .card-back .company-name {
    position: static; color: var(--on-red); font-size: 52px;
  }
  .card-back .company-mark { background: var(--on-red); width: 16px; height: 16px; }
</style>
</head>
<body>
<main class="stage">
  <section class="card card-front" aria-label="Business card front">
    <div class="holder">
      <h1 class="holder-name">Marcus Havelden</h1>
      <p class="holder-title">Managing Director</p>
      <ul class="contact-list">
        <li class="contact-item">
          <svg class="contact-icon" viewBox="0 0 24 24" aria-hidden="true"><path fill="var(--brand-red)" d="M6.6 10.8a15 15 0 0 0 6.6 6.6l2.2-2.2a1 1 0 0 1 1-.25 11.4 11.4 0 0 0 3.6.57 1 1 0 0 1 1 1V20a1 1 0 0 1-1 1A17 17 0 0 1 3 4a1 1 0 0 1 1-1h3.5a1 1 0 0 1 1 1c0 1.25.2 2.45.57 3.57a1 1 0 0 1-.25 1z"/></svg>
          (555) 318-4720
        </li>
        <li class="contact-item">
          <svg class="contact-icon" viewBox="0 0 24 24" aria-hidden="true"><rect x="2" y="5" width="20" height="14" rx="1.5" fill="var(--brand-red)"/><path d="M3 6l9 7 9-7" fill="none" stroke="#fff" stroke-width="1.6"/></svg>
          hello@emberrealty.com
        </li>
        <li class="contact-item">
          <svg class="contact-icon" viewBox="0 0 24 24" aria-hidden="true"><g fill="none" stroke="var(--brand-red)" stroke-width="2"><circle cx="12" cy="12" r="9.5"/><path d="M2.5 12h19M12 2.5c3 3 3 16 0 19M12 2.5c-3 3-3 16 0 19"/></g></svg>
          www.emberrealty.com
        </li>
      </ul>
    </div>

    <p class="company-name"><span class="company-mark" aria-hidden="true"></span>Ember Realty Inc</p>

    <div class="divider"></div>
    <address class="office-address">
      Ember Realty Inc<br>
      48 Willow Crest Lane<br>
      Maple Grove, ON K7A 3B5
    </address>
  </section>

  <section class="card card-back" aria-label="Business card back">
    <p class="company-name"><span class="company-mark" aria-hidden="true"></span>Ember Realty Inc</p>
  </section>
</main>
</body>
</html>
```